Birchvale Gundogs

create website page for Labrador Retriever stud dog business.

Target Market(s)

Owners looking to breed their dogs that compete in NFS/PTL hunt tests.

Industry/Entity Type

Dog Training

Logo Text

Birchvale Gundogs - Stud Dogs

Number of Pages Required

1 page

Colors

Designer to choose colors to be used in the design.

Requirements
Must have
• link to or info from my dogs pedigree.
• Main dog I'm advertising. GRCH Zeke's Jump 5 Rounds FX
• http://www.fieldpuplineage.example/lineage.asp?id=71926
• also link to gundog tallies-- for pass information.
• Can update the pictures to that actual pictures once design is complete.

```html
<!DOCTYPE html>
<html lang="en">
<head>
<meta charset="utf-8">
<title>Birchvale Gundogs – Stud Dogs</title>
<link href="https://fonts.googleapis.com/css2?family=Lato:wght@400;700;900&family=Open+Sans:wght@400;600;700&display=swap" rel="stylesheet">
<style>
:root{
  --orange:#f39200;
  --orange-deep:#e2531a;
  --rust:#a8300e;
  --ink:#2a2a2a;
  --text:#555;
  --muted:#8a8a8a;
  --line:#dcdcdc;
  --faq-bg:#ececec;
  --footer:#2c2c2c;
  --footer-base:#1d1d1d;
  --white:#fff;
}
*{box-sizing:border-box;margin:0;padding:0}
html,body{width:1200px;height:3048px;overflow:hidden}
body{font-family:"Open Sans",Arial,sans-serif;color:var(--text);background:var(--white);position:relative}
a{color:inherit;text-decoration:none}
.section{position:absolute;left:0;width:1200px}
h2,h3,.logo,.nav a,.hero-title{font-family:"Lato",Arial,sans-serif}

/* header */
.site-header{top:0;height:100px;background:var(--white)}
.logo{position:absolute;left:120px;top:30px;font-size:38px;font-weight:900;color:var(--ink);letter-spacing:.3px}
.search-box{position:absolute;right:120px;top:38px;width:230px;height:30px;border:1px solid var(--line);border-radius:15px;font-size:12px;color:#aaa;padding:6px 14px}
.search-box svg{position:absolute;right:10px;top:7px}

/* nav */
.main-nav{top:100px;height:40px;background:var(--orange)}
.nav{display:flex;margin-left:120px;height:40px}
.nav a{color:var(--white);font-size:14px;font-weight:700;padding:0 16px;line-height:40px;text-transform:uppercase}
.nav a.active{background:var(--rust)}

/* hero */
.hero{top:140px;height:520px;background:linear-gradient(180deg,#4d5a3a 0%,#6f8a3e 45%,#8aa84a 70%,#5f7d2e 100%)}
.hero-title{position:absolute;top:130px;width:100%;text-align:center;color:var(--white);font-size:44px;font-weight:900;line-height:54px;text-transform:uppercase;text-shadow:0 2px 6px rgba(0,0,0,.4)}
.search-panel{position:absolute;left:240px;top:270px;width:720px;height:150px;background:rgba(168,48,14,.94)}
.search-panel h3{color:var(--white);text-align:center;font-size:26px;font-weight:700;margin-top:16px;text-transform:uppercase}
.search-fields{display:flex;justify-content:center;gap:20px;margin-top:16px}
.select{width:200px;height:30px;background:var(--white);font-size:12px;color:#666;padding:6px 10px;position:relative}
.select:after{content:"";position:absolute;right:10px;top:12px;border:5px solid transparent;border-top-color:#666}
.search-btn{position:absolute;left:285px;top:130px;width:150px;height:38px;background:var(--orange);color:var(--white);font-weight:700;font-size:15px;text-align:center;line-height:38px;text-transform:uppercase}
.dots{position:absolute;top:490px;width:100%;display:flex;justify-content:center;gap:8px}
.dots span{width:9px;height:9px;border-radius:50%;background:rgba(255,255,255,.6)}
.dots span.on{background:var(--white)}

/* featured */
.featured{top:660px;height:500px;background:var(--white)}
.section-title{text-align:center;font-size:32px;font-weight:700;color:var(--ink);text-transform:uppercase}
.featured .section-title{margin-top:60px}
.cards{position:absolute;left:145px;top:125px;display:flex;gap:16px}
.card{width:215px;height:305px;background:var(--white);box-shadow:0 2px 8px rgba(0,0,0,.15)}
.card-photo{height:190px;background:linear-gradient(160deg,#5b6a42,#2f2f2c 60%,#7a8a55)}
.card-body{padding:12px 14px}
.card h3{color:var(--orange-deep);font-size:16px;font-weight:700}
.card p{font-size:11px;line-height:15px;color:var(--muted);margin-top:4px}
.more{font-size:12px;color:var(--orange-deep);margin-top:6px;display:block}
.arrow{position:absolute;top:260px}

/* pedigree */
.pedigree{top:1160px;height:580px;background:linear-gradient(110deg,#f59b14 0%,#ef7d14 45%,#d9440f 100%)}
.pedigree h2{position:absolute;left:120px;top:70px;color:var(--white);font-size:28px;font-weight:700;text-transform:uppercase}
.ped-grid{position:absolute;left:120px;top:130px;display:grid;grid-template-columns:340px 340px;row-gap:30px;column-gap:20px}
.ped h3{color:var(--white);font-size:15px;font-weight:700;line-height:20px}
.ped p{color:#ffe7c8;font-size:11px;line-height:17px}
.ped p a{text-decoration:underline;color:var(--white)}
.btn-outline{position:absolute;left:120px;top:430px;width:150px;height:40px;border:2px solid var(--white);color:var(--white);text-align:center;line-height:36px;font-weight:700;font-size:13px;text-transform:uppercase}
.ped-photo{position:absolute;left:820px;top:100px;width:330px;height:330px;border-radius:50%;border:10px solid var(--white);background:radial-gradient(circle at 55% 45%,#2a2a28 0%,#2f3a24 35%,#6d8d3b 70%,#88a44b 100%)}

/* why */
.why{top:1740px;height:440px;background:var(--white)}
.why-photo{position:absolute;left:150px;top:40px;width:270px;height:360px;background:linear-gradient(170deg,#fff 0%,#e8b56a 30%,#d28b3c 60%,#f4f1ec 100%)}
.why-text{position:absolute;left:460px;top:60px;width:640px}
.why h2{font-size:32px;font-weight:700;color:var(--ink);text-transform:uppercase}
.why p{font-size:13px;line-height:22px;color:var(--muted);margin-top:16px}
.btn-solid{display:inline-block;margin-top:24px;width:150px;height:40px;background:var(--rust);color:var(--white);font-weight:700;font-size:13px;text-align:center;line-height:40px;text-transform:uppercase}

/* faq */
.faq{top:2180px;height:460px;background:var(--faq-bg)}
.faq .section-title{margin-top:40px}
.faq-list{position:absolute;left:220px;top:100px;width:760px}
.faq-q{height:40px;border-bottom:1px solid #cfcfcf;font-size:13px;line-height:40px;padding-left:14px;color:#444;background:var(--white)}
.faq-q.open{background:var(--rust);color:var(--white);border:none}
.faq-a{background:var(--white);padding:14px;font-size:11px;line-height:17px;color:var(--muted);border-bottom:1px solid #cfcfcf}
.faq-a a{color:var(--orange-deep);text-decoration:underline}
.faq-dog-left{position:absolute;left:0;top:150px;width:210px;height:310px;background:linear-gradient(180deg,#e7e7e7,#2a2a2a 40%,#1d1d1d)}
.faq-dog-right{position:absolute;left:980px;top:200px;width:220px;height:260px;background:linear-gradient(180deg,#e7e7e7 0%,#2a2a2a 40%,#c8332a 80%,#e04a3a 100%)}

/* footer */
.site-footer{top:2640px;height:368px;background:var(--footer)}
.foot-col{position:absolute;top:50px;color:#cfcfcf}
.foot-col h3{color:var(--white);font-size:20px;font-weight:700;margin-bottom:18px}
.foot-col li{list-style:none;font-size:13px;line-height:26px}
.contact li{display:flex;gap:8px;align-items:flex-start}
.contact svg{margin-top:6px;flex:none}
.social{display:flex;gap:10px}
.social span{width:32px;height:32px;border-radius:50%;border:2px solid var(--white)}
.footer-base{top:3008px;height:40px;background:var(--footer-base);text-align:center;color:#999;font-size:12px;line-height:40px}
</style>
</head>
<body>

<header class="section site-header">
  <div class="logo">Birchvale Gundogs</div>
  <div class="search-box">Search here
    <svg width="14" height="14" viewBox="0 0 14 14"><circle cx="6" cy="6" r="4.5" fill="none" stroke="#999" stroke-width="1.6"/><line x1="9.5" y1="9.5" x2="13" y2="13" stroke="#999" stroke-width="1.6"/></svg>
  </div>
</header>

<nav class="section main-nav">
  <div class="nav">
    <a class="active">Home</a><a>About Us</a><a>Featured Dogs</a><a>Pedigrees</a><a>Help</a><a>My Litters</a><a>Test Breeding</a><a>Contact</a>
  </div>
</nav>

<section class="section hero" role="img" aria-label="Black Labrador retriever sitting on grass">
  <h1 class="hero-title">Anyone can search pedigrees,<br>litters &amp; stud dogs</h1>
  <div class="search-panel">
    <h3>Search for Labrador Retriever Litter</h3>
    <div class="search-fields">
      <div class="select">Select Breed</div>
      <div class="select">Location</div>
      <div class="select">Color</div>
    </div>
    <div class="search-btn">Search Now</div>
  </div>
  <div class="dots"><span class="on"></span><span></span><span></span><span></span></div>
</section>

<section class="section featured">
  <h2 class="section-title">Featured Dog</h2>
  <svg class="arrow" style="left:100px" width="20" height="34" viewBox="0 0 20 34"><polyline points="17,2 3,17 17,32" fill="none" stroke="#999" stroke-width="3"/></svg>
  <svg class="arrow" style="left:1080px" width="20" height="34" viewBox="0 0 20 34"><polyline points="3,2 17,17 3,32" fill="none" stroke="#999" stroke-width="3"/></svg>
  <div class="cards">
    <article class="card"><div class="card-photo" role="img" aria-label="Black Labrador retriever portrait"></div><div class="card-body"><h3>Dog Title here</h3><p>Strong field dog with steady marks, calm nature and proven hunt test passes.</p><span class="more">More Info »</span></div></article>
    <article class="card"><div class="card-photo" role="img" aria-label="Black Labrador retriever in the field"></div><div class="card-body"><h3>Dog Title here</h3><p>Strong field dog with steady marks, calm nature and proven hunt test passes.</p><span class="more">More Info »</span></div></article>
    <article class="card"><div class="card-photo" role="img" aria-label="Black Labrador retriever sitting"></div><div class="card-body"><h3>Dog Title here</h3><p>Strong field dog with steady marks, calm nature and proven hunt test passes.</p><span class="more">More Info »</span></div></article>
    <article class="card"><div class="card-photo" role="img" aria-label="Labrador retriever carrying a bird"></div><div class="card-body"><h3>Dog Title here</h3><p>Strong field dog with steady marks, calm nature and proven hunt test passes.</p><span class="more">More Info »</span></div></article>
  </div>
</section>

<section class="section pedigree">
  <h2>Dog Food Pedigree</h2>
  <div class="ped-grid">
    <div class="ped"><h3>GRCH Zeke's Jump 5 Rounds FX ( BLK )</h3><p>Reg: SR 41827605<br><a href="http://www.fieldpuplineage.example/lineage.asp?id=71926">View full pedigree</a><br><a>Pass record on gundog tallies</a><br>Hips: Good<br>Eyes: Clear</p></div>
    <div class="ped"><h3>GRHRCH Tanner's Scoop Of Willowmere MH ( YLW )</h3><p>Reg: SR 53910274<br>Hips: Excellent<br>Elbows: Normal</p></div>
    <div class="ped"><h3>Fennel Out of the Reeds QAA ( BLK )</h3><p>Reg: SR 38264019<br>Hips: Good<br>Eyes: Clear</p></div>
    <div class="ped"><h3>FC-AFC Stillwater Maple II ( BLK )</h3><p>Reg: SR 29573816<br>Hips: Good</p></div>
  </div>
  <div class="btn-outline">View More</div>
  <div class="ped-photo" role="img" aria-label="Black Labrador retriever standing on grass"></div>
</section>

<section class="section why">
  <div class="why-photo" role="img" aria-label="Golden Labrador retriever eating from a bowl"></div>
  <div class="why-text">
    <h2>Why We Are</h2>
    <p>We raise and stand proven Labrador retrievers for owners who run their dogs in NFS and PTL hunt tests. Every stud is health tested and trained daily in water and upland work.</p>
    <p>Our breeding program focuses on natural drive, trainability and a sound, even temperament. Full pedigrees and test records are shared openly so you can plan a litter with confidence and clear expectations.</p>
    <div class="btn-solid">Read More</div>
  </div>
</section>

<section class="section faq">
  <h2 class="section-title">FAQ</h2>
  <div class="faq-dog-left" role="img" aria-label="Black Labrador retriever sitting"></div>
  <div class="faq-dog-right" role="img" aria-label="Black Labrador retriever beside a red food bowl"></div>
  <div class="faq-list">
    <div class="faq-q open">Q. How do I book a stud service with GRCH Zeke's Jump 5 Rounds FX?</div>
    <div class="faq-a">Send your female's pedigree and season date. See his lineage at <a href="http://www.fieldpuplineage.example/lineage.asp?id=71926">http://www.fieldpuplineage.example/lineage.asp?id=71926</a> and his passes on <a>gundog tallies</a>.</div>
    <div class="faq-q">Q. Are all your stud dogs health tested before breeding?</div>
    <div class="faq-q">Q. Where can I view full pedigree and test pass records?</div>
    <div class="faq-q">Q. Do you ship chilled or frozen semen?</div>
    <div class="faq-q">Q. What hunt test titles do your dogs hold?</div>
  </div>
</section>

<footer class="section site-footer">
  <div class="foot-col" style="left:120px"><h3>Quick Links</h3><ul><li>Home</li><li>About Us</li><li>Search Litters</li><li>Featured Dogs</li></ul></div>
  <div class="foot-col" style="left:380px"><h3>Resources</h3><ul><li>FAQ</li><li>Help</li><li>Litter Blog</li><li>Contact Us</li></ul></div>
  <div class="foot-col contact" style="left:640px"><h3>Contact Us</h3><ul>
    <li><svg width="10" height="13" viewBox="0 0 10 13"><path d="M5 0a5 5 0 0 0-5 5c0 4 5 8 5 8s5-4 5-8a5 5 0 0 0-5-5z" fill="#cfcfcf"/><circle cx="5" cy="5" r="1.8" fill="#2c2c2c"/></svg><span>1410 Fernhill Road,<br>Dayton, OH 45402</span></li>
    <li><svg width="12" height="12" viewBox="0 0 12 12"><path d="M2 0l2.5 3-1.5 1.5a8 8 0 0 0 4.5 4.5L9 7.5l3 2.5-2 2C5 12 0 7 0 2z" fill="#cfcfcf"/></svg><span>555-014-2290</span></li>
    <li><svg width="13" height="10" viewBox="0 0 13 10"><rect x=".5" y=".5" width="12" height="9" fill="none" stroke="#cfcfcf"/><polyline points=".5,.5 6.5,5.5 12.5,.5" fill="none" stroke="#cfcfcf"/></svg><span>info@birchvalegundogs.example</span></li>
  </ul></div>
  <div class="foot-col" style="left:930px"><h3>Follow Us</h3><div class="social"><span></span><span></span><span></span><span></span></div></div>
</footer>
<div class="section footer-base">© 2017 Birchvale Gundogs. All Right Reserved. Terms of Use</div>

</body>
</html>
```